KRT Flyer - Workshop and Scholarship Program

KRT needs a double sided flyer designed for an upcoming workshop we have that is also doubling as a launch of our business and of our scholarship program.
All of the information required to go onto the flyer is contained below in the two documents.
The first is a word document that contains the details to be included on the flyer - this is in the order that I wish to present them also.
The second document is an earlier example of a winning flyer that was designed for an earlier launch. I was happy with many of the characteristics within this flyer including the photo/bio at the bottom.
Please note that the language and descriptions have all changed.
Please use images and patterns that you feel address the requirements of the advertisement.
I have included the original design files for the logo and flyer to get the logo and bio image
Target Market(s)
HSC students (Final Year of High School
Industry/Entity Type
Education
Font styles to use
Other font styles liked:
- Myriad Pro
Requirements
Must have
- The logo of the business must be shown a maximum of twice on both sides. Please remove the surrounding square and imbed it into the flyer.
- A simple but effective design
Nice to have
- Images that reflect the content
Should not have
- Too much going on that the message is lost.

```html
<!DOCTYPE html>
<html lang="en">
<head>
<meta charset="utf-8">
<title>KRT – 2017 Free HSC Preparation Workshop Flyer</title>
<link href="https://fonts.googleapis.com/css2?family=Source+Sans+3:wght@400;600;700;900&display=swap" rel="stylesheet">
<style>
:root{
  --page:#e9e9ec;
  --purple-deep:#3b2a78;
  --purple:#5a3f98;
  --violet:#7a5cb8;
  --blue:#3f63b8;
  --blue-light:#6b8fd8;
  --lavender:#c4b6e2;
  --teal:#41c4b4;
  --white:#ffffff;
  --ink:#2c2456;
  --photo-warm:#e8c9a8;
  --photo-cool:#9bb4d6;
}
*{box-sizing:border-box;margin:0;padding:0}
html,body{width:1200px;height:896px;overflow:hidden;background:var(--page)}
body{font-family:"Source Sans 3",sans-serif;color:var(--white)}
.flyer{position:absolute;left:300px;top:24px;width:600px;height:848px;overflow:hidden;
  background:linear-gradient(160deg,var(--blue-light) 0%,var(--blue) 40%,var(--purple) 75%,var(--purple-deep) 100%)}
.hero-photo{position:absolute;left:0;top:0;width:600px;height:360px;
  background:linear-gradient(120deg,#f3efe9 0%,var(--photo-warm) 35%,#8fa9cf 65%,var(--photo-cool) 100%)}
.shapes{position:absolute;left:0;top:0}
.brand{position:absolute;left:22px;top:20px;display:flex;align-items:center;gap:8px}
.brand-dot{width:30px;height:30px;border-radius:50%;background:var(--purple)}
.brand-name{font-weight:700;font-size:24px;color:var(--purple)}
.badge{position:absolute;left:440px;top:70px;width:140px;height:140px;border-radius:50%;
  border:3px solid rgba(255,255,255,.85)}
.headline{position:absolute;left:28px;top:262px;width:320px;line-height:.95}
.headline .big{display:block;font-weight:900;font-size:42px;text-transform:uppercase}
.headline .free{color:var(--teal)}
.headline .sub{display:block;font-weight:600;font-size:27px;text-transform:uppercase;margin-top:4px;line-height:1}
.register{position:absolute;left:26px;top:472px;width:236px;height:236px;border-radius:50%;
  background:var(--lavender);color:var(--ink);padding:40px 32px 0 40px}
.register h2{font-weight:700;font-size:26px;line-height:1;text-transform:uppercase;color:var(--purple)}
.register p{font-size:12.5px;line-height:1.3;margin-top:8px}
.turn-over{position:absolute;left:206px;top:640px;width:96px;height:96px;border-radius:50%;
  background:var(--purple-deep);font-size:9px;line-height:1.25;padding:20px 10px;text-align:center}
.day{position:absolute;left:350px;top:428px;width:232px}
.day h2{font-weight:700;font-size:23px;line-height:1;text-transform:uppercase}
.day ul{list-style:none;margin-top:7px}
.day li{font-size:10.5px;line-height:1.2;padding-left:11px;position:relative;margin-bottom:2px}
.day li::before{content:"";position:absolute;left:0;top:4px;width:5px;height:5px;border-radius:50%;background:var(--teal)}
.session{position:absolute;left:370px;width:212px;background:var(--white);color:var(--ink);
  border-collapse:collapse;font-size:9.5px}
.session th{background:var(--purple);color:var(--white);text-align:left;font-weight:600;padding:2px 6px;width:58px;vertical-align:top;line-height:1.2}
.session td{padding:2px 6px;border-bottom:1px solid #ddd;line-height:1.2}
.session-one{top:598px}
.session-two{top:690px}
.bio-photo{position:absolute;left:30px;top:700px;width:170px;height:86px;border-radius:8px;
  background:linear-gradient(150deg,#f2ebe4 0%,#d9b89a 50%,#8aa0c8 100%)}
.bio{position:absolute;left:0;bottom:0;width:600px;height:58px;background:var(--white);color:var(--ink);
  font-size:10.5px;line-height:1.3;padding:8px 24px 0 220px}
</style>
</head>
<body>
<main class="flyer">
  <div class="hero-photo" role="img" aria-label="Photo of a smiling group of senior high school students holding books"></div>

  <svg class="shapes" width="600" height="848" viewBox="0 0 600 848" aria-hidden="true">
    <polygon points="0,250 420,230 360,440 0,470" fill="#5a3f98" opacity=".88"/>
    <polygon points="0,330 260,300 190,470 0,520" fill="#3b2a78" opacity=".55"/>
    <polygon points="330,360 600,300 600,560 300,520" fill="#3f63b8" opacity=".8"/>
    <polygon points="260,420 600,470 600,848 380,848" fill="#3b2a78" opacity=".35"/>
    <polygon points="0,600 220,560 160,848 0,848" fill="#7a5cb8" opacity=".4"/>
  </svg>

  <div class="brand">
    <span class="brand-dot"></span>
    <span class="brand-name">KRT</span>
  </div>

  <div class="badge" aria-hidden="true"></div>

  <h1 class="headline">
    <span class="big">2017</span>
    <span class="big"><span class="free">Free</span> HSC</span>
    <span class="big">Preparation</span>
    <span class="sub">Workshop and<br>Scholarship Offer</span>
  </h1>

  <section class="register">
    <h2>How to<br>register:</h2>
    <p>Text 0400 123 456 with your name, email address and the session date and time you wish to attend. An email will then be sent confirming further details.</p>
  </section>

  <p class="turn-over">Turn over to read about the inaugural Bright Path Scholarship Program</p>

  <section class="day">
    <h2>What will<br>the day<br>involve?</h2>
    <ul>
      <li>Setting personal goals for the year ahead</li>
      <li>Building the right mindset for the HSC</li>
      <li>Working through a practice exam task</li>
      <li>Knowing the value of steady study habits</li>
      <li>Ways to lift your study and beat procrastination</li>
    </ul>
  </section>

  <table class="session session-one">
    <tr><th>Date</th><td>Monday 2nd October 2017</td></tr>
    <tr><th>Location</th><td>Riverside</td></tr>
    <tr><th>Time</th><td>Session 1 – 9am – 12pm<br>Session 2 – 1pm – 4pm</td></tr>
    <tr><th>Cost</th><td>FREE* – limited seats</td></tr>
  </table>

  <table class="session session-two">
    <tr><th>Date</th><td>Tuesday 3rd October 2017</td></tr>
    <tr><th>Location</th><td>Northbank</td></tr>
    <tr><th>Time</th><td>Session 1 – 9am – 12pm<br>Session 2 – 1pm – 4pm</td></tr>
    <tr><th>Cost</th><td>FREE* – limited seats</td></tr>
  </table>

  <div class="bio-photo" role="img" aria-label="Portrait photo of the tutor in a light blue shirt"></div>

  <p class="bio">I have worked as both a teacher and tutor in Sydney and other parts of New South Wales for the last 7 years. I have helped many students reach their best results in the HSC.</p>
</main>
</body>
</html>
```